Meridale Partners Website

Meridale Partners (MP) provide Analytics & Enterprise Performance Management (EPM) advisory & consultancy services. We are passionate about data and making a difference for our clients by working in partnership with them, helping them on their journey to becoming an Meridale Partner. We deliver insights which give our clients a competitive edge and a much deeper understanding of their organisation.

We need a website which shows who we are, what we do and how we do it.

www.meridale-partners.example is our very basic website at the moment. We want to completely revamp it with a corporate look

```html
<!DOCTYPE html>
<html lang="en">
<head>
<meta charset="utf-8">
<title>Meridale Partners</title>
<link href="https://fonts.googleapis.com/css2?family=Poppins:wght@400;500;600;700&family=PT+Sans:wght@400;700&display=swap" rel="stylesheet">
<style>
:root{
  --navy:#1e3f5a;
  --navy-deep:#12283b;
  --ink:#111c26;
  --footer:#0b141c;
  --cyan:#27b5d8;
  --red:#ee3e1f;
  --slate:#2f3447;
  --pale:#e6eef5;
  --text:#333b44;
  --muted:#555d66;
  --white:#ffffff;
}
*{margin:0;padding:0;box-sizing:border-box}
html,body{width:1200px;height:4370px;overflow:hidden}
body{position:relative;background:var(--white);font-family:"Poppins",sans-serif;color:var(--text)}
.abs{position:absolute}
.heading{font-family:"PT Sans",sans-serif;font-weight:700;text-transform:uppercase;color:var(--ink)}
.heading span{color:var(--navy)}
.btn{position:absolute;display:flex;align-items:center;justify-content:center;background:var(--navy);color:var(--white);font-weight:600;font-size:14px;border-radius:0 10px 0 10px;text-transform:uppercase}

/* header */
.site-header{left:0;top:0;width:1200px;height:93px;background:var(--white)}
.brand{left:107px;top:20px;display:flex;align-items:center;gap:14px}
.brand-mark{width:48px;height:48px;border-radius:50%;border:7px solid var(--navy)}
.brand-name{font-weight:600;font-size:18px;line-height:20px;color:var(--navy);letter-spacing:.5px}
.nav{left:360px;top:36px;display:flex;gap:30px;font-size:15px;color:var(--ink)}
.nav .active{font-weight:600;color:var(--navy)}
.lang{left:870px;top:36px;display:flex;align-items:center;gap:8px;font-size:14px}
.lang i{width:26px;height:26px;border-radius:50%;background:linear-gradient(90deg,#2e9b4a 33%,#fff 33% 66%,#f08a24 66%)}
.login{left:995px;top:30px;width:97px;height:36px}

/* hero */
.hero{left:0;top:93px;width:1200px;height:700px;overflow:hidden}
.hero-photo{position:absolute;inset:0;background:linear-gradient(100deg,#d9dfe0 0%,#c8cdca 35%,#b8b9b4 55%,#8f8e8a 75%,#d7dadb 100%)}
.hero h1{left:111px;top:292px;font-size:41px;line-height:54px}
.hero h1 span{color:var(--navy)}
.hero-copy{left:111px;top:410px;width:330px;font-size:15px;line-height:24px;color:var(--ink)}
.hero-btn{left:111px;top:505px;width:124px;height:34px;font-size:13px}

/* services */
.services-title{left:0;top:862px;width:1200px;text-align:center;font-size:30px}
.card{position:absolute;top:955px;width:298px;height:338px;background:var(--white);border-radius:0 40px 0 40px;box-shadow:0 4px 18px rgba(0,0,0,.13);text-align:center;padding-top:36px}
.card.featured{background:var(--navy);color:var(--white)}
.card-icon{width:100px;height:100px;margin:0 auto 18px;background:var(--navy);border-radius:12px;opacity:.9}
.card.featured .card-icon{background:var(--white)}
.card h3{font-family:"PT Sans",sans-serif;font-size:21px;line-height:27px;color:var(--navy);margin-bottom:14px}
.card.featured h3{color:var(--white)}
.card p{font-size:13px;line-height:22px;padding:0 34px;color:var(--muted)}
.card.featured p{color:#dfe7ee}

/* about */
.about{left:0;top:1382px;width:1200px;height:641px;background:linear-gradient(120deg,#e9f0f6,#d8e3ec 60%,#e4ecf2)}
.about-photo{left:112px;top:125px;width:408px;height:335px;background:linear-gradient(135deg,#b9c3c8,#6b6a63 60%,#3c3530);border-radius:8px;border:3px solid var(--white)}
.about-video{left:400px;top:356px;width:180px;height:163px;background:linear-gradient(135deg,#4c5660,#22292f);border-radius:4px}
.play{left:70px;top:62px;width:42px;height:42px;border-radius:50%;background:var(--white)}
.play::after{content:"";position:absolute;left:16px;top:12px;border-left:14px solid var(--ink);border-top:9px solid transparent;border-bottom:9px solid transparent}
.call{left:110px;top:480px;display:flex;align-items:center;gap:14px;font-weight:600;font-size:15px;color:var(--navy)}
.call i{width:38px;height:38px;border-radius:50%;background:var(--navy);display:flex;align-items:center;justify-content:center}
.about h2{left:622px;top:132px;font-size:31px}
.about-copy{left:620px;top:180px;width:468px;font-family:"PT Sans",sans-serif;font-size:16px;line-height:25.5px;text-align:justify;color:var(--text)}
.about-copy p{margin-bottom:7px}
.about-btn{left:622px;top:463px;width:130px;height:38px}

/* how */
.how{left:0;top:2023px;width:1200px;height:817px;background:linear-gradient(180deg,#fbfcfd,#f1f4f7)}
.how h2{left:0;top:90px;width:1200px;text-align:center;font-size:30px}
.process-graphic{left:335px;top:150px;width:520px;height:480px;border-radius:24px;background:linear-gradient(135deg,#cdeef6 0%,#e9edf2 50%,#f7d6cf 75%,#d3d5dc 100%)}
.step-title{font-size:25px;font-weight:500}
.step-copy{font-size:13.5px;line-height:22px;color:var(--text)}

/* discuss */
.discuss{left:0;top:2840px;width:1200px;height:470px;background:var(--navy)}
.discuss-photo{left:600px;top:0;width:600px;height:470px;background:linear-gradient(135deg,#6e8aa0,#2a3540 55%,#1a2128);border-radius:470px 0 0 470px/470px 0 0 470px}
.discuss h2{left:67px;top:86px;color:var(--white);font-size:30px;line-height:42px}
.discuss-copy{left:67px;top:176px;width:485px;font-size:13.5px;line-height:25.5px;color:#e4ebf1;text-align:justify}
.outline-btn{left:67px;top:345px;width:118px;height:40px;border:2px solid var(--white);border-radius:0 10px 0 10px;color:var(--white);font-weight:600;font-size:13px;display:flex;align-items:center;justify-content:center}

/* contact */
.contact-title{left:0;top:3375px;width:1200px;text-align:center;font-size:30px}
.corner{left:147px;top:3445px;width:133px;height:100px;border-left:14px solid var(--navy);border-top:14px solid var(--navy)}
.form-card{left:160px;top:3460px;width:518px;height:415px;background:var(--white);box-shadow:0 4px 22px rgba(0,0,0,.12)}
.field{position:absolute;height:34px;border:1px solid #a9b0b7;font-size:11px;padding:9px 8px;color:var(--ink)}
.submit{left:40px;top:320px;width:98px;height:38px}
.info{left:728px;display:flex;gap:16px}
.info i{width:34px;height:34px;border-radius:50%;background:var(--navy);flex:none;display:flex;align-items:center;justify-content:center}
.info b{display:block;font-size:13px;color:var(--ink)}
.info span{font-size:15px;line-height:24px;color:var(--ink)}
.follow{left:734px;top:3740px;font-weight:700;font-size:16px;color:var(--ink)}
.socials{left:734px;top:3775px;display:flex;gap:12px}
.socials i{width:29px;height:29px;border-radius:50%;background:var(--navy)}

/* footer */
.footer{left:0;top:3990px;width:1200px;height:380px}
.footer-col{color:var(--white)}
.footer-col h4{font-size:20px;font-weight:600;margin-bottom:14px}
.footer-col a{display:block;font-size:15px;line-height:33px;color:#e5ecf2}
.newsletter{left:830px;top:128px;width:260px;height:42px;border:1px solid #c9d2da;font-size:12px;color:var(--white);padding:12px 16px}
.partner{left:832px;top:200px;display:flex;align-items:center;gap:12px;color:var(--white);font-size:14px}
.partner i{width:22px;height:22px;background:#c9d2da}
.copyright{left:0;top:330px;width:1200px;text-align:center;font-size:15px;color:#dde4ea}
</style>
</head>
<body>

<header class="abs site-header">
  <div class="abs brand"><div class="brand-mark"></div><div class="brand-name">MERIDALE<br>PARTNERS</div></div>
  <nav class="abs nav"><span class="active">Home</span><span>Services</span><span>About Us</span><span>How We Do It</span><span>Contact Us</span></nav>
  <div class="abs lang"><i></i><span>⌄ ENG</span></div>
  <div class="btn login">Log In</div>
</header>

<section class="abs hero">
  <div class="hero-photo" role="img" aria-label="Office scene with a consultant in a suit, colleagues working at laptops behind"></div>
  <svg class="abs" style="left:0;top:0" width="1200" height="700" viewBox="0 0 1200 700">
    <path d="M0 560 Q140 700 560 690 Q900 680 1200 590 L1200 700 L0 700Z" fill="#fff"/>
    <path d="M0 560 Q140 690 560 678 Q900 668 1200 590 L1200 600 Q900 686 560 692 Q140 700 0 580Z" fill="#1e3f5a"/>
  </svg>
  <h1 class="abs heading">Welcome to<br><span>Meridale Partners</span></h1>
  <p class="abs hero-copy">MP are a Data Analytics &amp; EPM company, specialising in the implementation and support of Business Intelligence.</p>
  <div class="btn hero-btn">Get Started</div>
</section>

<h2 class="abs heading services-title">Our <span>Services</span></h2>
<div class="card" style="left:110px"><div class="card-icon" role="img" aria-label="Consultant icon"></div><h3>Advise &amp;<br>Architect Services</h3><p>Helping our customers understand the art of the possible and safeguarding their investments by overseeing implementations.</p></div>
<div class="card featured" style="left:446px"><div class="card-icon" role="img" aria-label="Design tool icon"></div><h3>Design &amp;<br>Implement</h3><p>Working with the project management team, through each stage of the project, with clearly defined deliverables and well</p></div>
<div class="card" style="left:781px"><div class="card-icon" role="img" aria-label="Code window with gear icon"></div><h3>Optimise &amp;<br>Manage</h3><p>Our Managed Services delivers proactive, on-demand support for EPM and Data Analytics environments</p></div>

<section class="abs about">
  <div class="abs about-photo" role="img" aria-label="Three colleagues reviewing documents around a laptop"></div>
  <div class="abs about-video" role="img" aria-label="Video thumbnail of an analytics dashboard on a laptop"><div class="abs play"></div></div>
  <div class="abs call"><i><svg width="18" height="18" viewBox="0 0 24 24"><path fill="#fff" d="M6.6 10.8a15 15 0 0 0 6.6 6.6l2.2-2.2c.3-.3.7-.4 1-.2 1.1.4 2.3.6 3.6.6.6 0 1 .4 1 1V20c0 .6-.4 1-1 1A17 17 0 0 1 3 4c0-.6.4-1 1-1h3.5c.6 0 1 .4 1 1 0 1.3.2 2.5.6 3.6.1.3 0 .7-.2 1z"/></svg></i>CALL US ON 01 555 0142</div>
  <h2 class="abs heading">About <span>Meridale Partners</span></h2>
  <div class="abs about-copy">
    <p>Meridale Partners is an exciting start-up in the Data Analytics and EPM space. Founded in 2019, MP specialise in the implementation and support of BI, EPM and Data Analytics business solutions, both in the Cloud and on-premise.</p>
    <p>Lorem ipsum dolor sit amet, consectetur adipiscing elit, sed do eiusmod tempor incididunt ut labore et dolore magna aliqua.</p>
    <p>Lorem ipsum dolor sit amet, consectetur adipiscing elit, sed do eiusmod tempor incididunt ut labore et dolore magna aliqua. Ut enim ad minim veniam, quis nostrud exercitation ullamco laboris nisi ut aliquip ex ea commodo consequat.</p>
  </div>
  <div class="btn about-btn">Read More</div>
</section>

<section class="abs how">
  <h2 class="abs heading">How <span>We Do It</span></h2>
  <div class="abs process-graphic" role="img" aria-label="Process illustration of three linked stages: advisory, the partnership, and analytics"></div>
  <div class="abs step-title" style="left:717px;top:183px;color:var(--cyan)">Meridale Partners</div>
  <p class="abs step-copy" style="left:717px;top:225px;width:360px">Lorem ipsum dolor sit amet, consectetur adipiscing elit, sed do eiusmod tempor incididunt ut labore et dolore magna aliqua.</p>
  <div class="abs step-title" style="left:118px;top:310px;color:var(--red);font-weight:600;font-size:23px">ADVISORY &amp; CONSULTANCY</div>
  <p class="abs step-copy" style="left:106px;top:352px;width:340px;text-align:right">Lorem ipsum dolor sit amet, consectetur elit, sed do eiusmod tempor incididunt ut labore et dolore magna aliqua.</p>
  <div class="abs step-title" style="left:752px;top:636px;color:var(--slate)">Provide Analytics</div>
  <p class="abs step-copy" style="left:752px;top:678px;width:345px">Lorem ipsum dolor sit amet, consectetur adipiscing elit, sed do eiusmod tempor incididunt ut labore et dolore magna aliqua.</p>
</section>

<section class="abs discuss">
  <div class="abs discuss-photo" role="img" aria-label="Team meeting around a boardroom table in a glass office"></div>
  <h2 class="abs heading">Discuss your business<br>needs:</h2>
  <p class="abs discuss-copy">Lorem ipsum dolor sit amet, consectetur adipiscing elit, sed do eiusmod tempor incididunt ut labore et dolore magna aliqua. Ut enim ad minim veniam, quis nostrud exercitation ullamco laboris nisi ut aliquip ex ea commodo consequat. Lorem ipsum dolor sit amet, consectetur adipiscing elit, sed do eiusmod tempor incididunt ut labore et dolore magna aliqua. Ut enim ad minim veniam.</p>
  <div class="abs outline-btn">LEARN MORE</div>
</section>

<h2 class="abs heading contact-title">Contact <span>Us</span></h2>
<div class="abs corner"></div>
<form class="abs form-card">
  <div class="field" style="left:40px;top:55px;width:212px">First Name:</div>
  <div class="field" style="left:268px;top:55px;width:212px">Last name:</div>
  <div class="field" style="left:40px;top:107px;width:212px">Phone Number:</div>
  <div class="field" style="left:268px;top:107px;width:212px">Address:</div>
  <div class="field" style="left:40px;top:159px;width:440px;height:52px">I'm interested in*:</div>
  <div class="field" style="left:40px;top:228px;width:440px;height:72px">Message:</div>
  <div class="btn submit">Submit</div>
</form>
<div class="abs info" style="top:3485px"><i><svg width="14" height="18" viewBox="0 0 14 20"><path fill="#fff" d="M7 0a7 7 0 0 0-7 7c0 5 7 13 7 13s7-8 7-13a7 7 0 0 0-7-7zm0 9.5A2.5 2.5 0 1 1 7 4.5a2.5 2.5 0 0 1 0 5z"/></svg></i><div><b>Address :</b><span>14 Harbour Row, Quayside,<br>Dockford 3, QX4 7LM</span></div></div>
<div class="abs info" style="top:3570px"><i><svg width="16" height="16" viewBox="0 0 24 24"><path fill="#fff" d="M6.6 10.8a15 15 0 0 0 6.6 6.6l2.2-2.2c.3-.3.7-.4 1-.2 1.1.4 2.3.6 3.6.6.6 0 1 .4 1 1V20c0 .6-.4 1-1 1A17 17 0 0 1 3 4c0-.6.4-1 1-1h3.5c.6 0 1 .4 1 1 0 1.3.2 2.5.6 3.6.1.3 0 .7-.2 1z"/></svg></i><div><b>Phone Number :</b><span>01 555 0142</span></div></div>
<div class="abs info" style="top:3642px"><i><svg width="16" height="12" viewBox="0 0 16 12"><rect width="16" height="12" rx="1" fill="#fff"/><path d="M1 1l7 6 7-6" fill="none" stroke="#1e3f5a" stroke-width="1.5"/></svg></i><div><b>Email :</b><span>info@meridale-partners.example</span></div></div>
<div class="abs follow">FOLLOW US</div>
<div class="abs socials"><i></i><i></i><i></i><i></i></div>

<footer class="abs footer">
  <svg class="abs" style="left:0;top:0" width="1200" height="380" viewBox="0 0 1200 380">
    <path d="M0 75 Q600 -40 1200 60 L1200 380 L0 380Z" fill="#1e3f5a"/>
    <path d="M0 88 Q600 -10 1200 75 L1200 380 L0 380Z" fill="#0b141c"/>
  </svg>
  <div class="abs brand" style="left:107px;top:88px"><div class="brand-mark" style="width:64px;height:64px;border-color:#fff"></div><div class="brand-name" style="color:#fff;font-size:22px;line-height:26px">MERIDALE<br>PARTNERS</div></div>
  <div class="abs footer-col" style="left:405px;top:84px"><h4>Quick Link</h4><a>Home</a><a>Services</a><a>About Us</a><a>How We Do It</a><a>Contact Us</a></div>
  <div class="abs footer-col" style="left:570px;top:84px"><h4>Our Services</h4><a>Advise &amp; Architect Services</a><a>Design &amp; Implement</a><a>Optimise &amp; Manage</a></div>
  <div class="abs footer-col" style="left:830px;top:84px"><h4>Newsletter</h4></div>
  <div class="abs newsletter">Enter Email</div>
  <div class="abs partner"><i></i><span style="font-weight:600">CORVANE</span><span style="border-left:1px solid #c9d2da;padding-left:12px">Partner</span></div>
  <div class="abs copyright">© 2022 meridale | All rights reserved.</div>
</footer>

</body>
</html>
```